The most modern business card ever !!!

Our company call “Vendalo”. Vendalo is a technology company specialized in cruises solutions. Out main product is a platform to reserve cruises. This is a revolutionary platform that make easier to travel agencies and final users to reserve cruises across dozen companies like tibba, wernu, hpv, dgb, etc..We are a “start up”, with a young team of developers and we want to transmit it.. For it, we want something different, a modern business card that represent cruises and technology.. When someone receive this card, this person should say: wowww this is different… this is modern… this is a cruise related company..
- diferent, modern
- traditions business card

```html
<!DOCTYPE html>
<html lang="en">
<head>
<meta charset="utf-8">
<title>Vendalo – Business Card</title>
<link href="https://fonts.googleapis.com/css2?family=Open+Sans:wght@400;600;700&display=swap" rel="stylesheet">
<style>
  :root {
    --stage: #4a4a4a;
    --card-white: #ffffff;
    --brand-blue: #29a9e1;
    --ink: #111111;
    --text-grey: #3c3c3c;
    --rule: #c9c9c9;
    --logo-light: #e6f5fc;
  }
  * { margin: 0; padding: 0; box-sizing: border-box; }
  html, body {
    width: 1200px; height: 900px; overflow: hidden;
    background: var(--stage);
    font-family: "Open Sans", Arial, sans-serif;
  }
  .stage { position: relative; width: 1200px; height: 900px; }
  .card {
    position: absolute;
    width: 477px; height: 294px;
    box-shadow: 2px 3px 4px rgba(0,0,0,0.55);
  }
  .card--front {
    left: 120px; top: 275px;
    background: var(--card-white);
    border-radius: 0 50px 0 50px;
  }
  .card--back {
    left: 607px; top: 274px;
    background: var(--brand-blue);
    border-radius: 50px 0 50px 0;
  }
  .wordmark {
    position: absolute;
    font-weight: 600;
    letter-spacing: 1px;
    line-height: 1;
  }
  .card--front .wordmark {
    left: 30px; top: 122px;
    font-size: 44px; color: var(--ink);
  }
  .card--back .wordmark {
    left: 0; right: 0; top: 122px;
    text-align: center;
    font-size: 48px; color: var(--logo-light);
  }
  .divider {
    position: absolute;
    left: 242px; top: 75px;
    width: 1px; height: 145px;
    background: var(--rule);
  }
  .contact {
    position: absolute;
    left: 261px; top: 72px;
    color: var(--text-grey);
  }
  .contact__name {
    font-size: 15px; font-weight: 700;
    color: var(--brand-blue);
    letter-spacing: 0.3px; line-height: 19px;
  }
  .contact__role { font-size: 13.5px; line-height: 16px; margin-bottom: 6px; }
  .contact__list { list-style: none; }
  .contact__item {
    display: flex; align-items: center;
    font-size: 13.5px; line-height: 17.3px;
  }
  .contact__icon { width: 10px; height: 10px; margin-right: 4px; flex: none; }
  .contact__address { font-size: 14px; line-height: 17px; margin-top: 6px; }
</style>
</head>
<body>
<main class="stage">
  <section class="card card--front">
    <div class="wordmark">Vendalo</div>
    <div class="divider"></div>
    <div class="contact">
      <div class="contact__name">MARCUS HALE</div>
      <div class="contact__role">Managing Director</div>
      <ul class="contact__list">
        <li class="contact__item">
          <svg class="contact__icon" viewBox="0 0 10 10" aria-hidden="true"><path d="M1 3.5C1 2 2.5 1.5 5 1.5S9 2 9 3.5L7.5 4V3.2H2.5V4Z M2.5 5H7.5L8.5 8.5H1.5Z" fill="#29a9e1"/></svg>
          044-987 654 321
        </li>
        <li class="contact__item">
          <svg class="contact__icon" viewBox="0 0 10 10" aria-hidden="true"><rect x="2.5" y="0.5" width="5" height="9" rx="1" fill="none" stroke="#29a9e1" stroke-width="1"/><circle cx="5" cy="8" r="0.6" fill="#29a9e1"/></svg>
          044-987 654 321
        </li>
        <li class="contact__item">
          <svg class="contact__icon" viewBox="0 0 10 10" aria-hidden="true"><rect x="0.5" y="2" width="9" height="6" fill="#29a9e1"/><path d="M0.5 2L5 5.5L9.5 2" fill="none" stroke="#fff" stroke-width="0.8"/></svg>
          hello@vendalo.io
        </li>
        <li class="contact__item">
          <svg class="contact__icon" viewBox="0 0 10 10" aria-hidden="true"><circle cx="5" cy="5" r="4.5" fill="#29a9e1"/><path d="M3 3.5L5 3L6 4.5L4.5 6L5 8M6.5 6.5L7.5 6" fill="none" stroke="#fff" stroke-width="0.8"/></svg>
          www.vendalo.io
        </li>
      </ul>
      <div class="contact__address">48 Harbour Lane, Dock 7<br>Portmarin, 204816.</div>
    </div>
  </section>
  <section class="card card--back">
    <div class="wordmark">Vendalo</div>
  </section>
</main>
</body>
</html>
```